Webdesign für Vertrieb und Verkauf von Vellorix Produkten im Firmenbereich
Zielgruppe
Vertrieb und Verkauf von Vellorix Produkten im Firmenbereich (Vellorix KLT, Quorent Flowdesk)
Aufgabenstellung
Ein Logo gibt es auf der bestehenden Internetseite https://www.kelbrotech.eu/ - Dieses Logo bitte beibehalten.
Ansonsten eine schnörkelloses klares Design welches Firmenkunden anspricht und wo man sich schnell zurecht findet.

```html
<!DOCTYPE html>
<html lang="de">
<head>
<meta charset="utf-8">
<title>Kelbro – Vellorix KLT wird Quorent Flowdesk</title>
<link href="https://fonts.googleapis.com/css2?family=Montserrat:wght@300;400;500;600;700&family=Mulish:wght@400;600;700&display=swap" rel="stylesheet">
<style>
:root{
  --pink:#c04a78;
  --pink-dark:#b43d6b;
  --pink-light:#d67b9e;
  --blush:#fcf0f5;
  --ink:#1f1f24;
  --text:#6b6b72;
  --muted:#9a9aa2;
  --grey-band:#f3f3f4;
  --white:#ffffff;
}
*{box-sizing:border-box;margin:0;padding:0}
html,body{width:1200px;height:3720px;overflow:hidden;background:var(--white)}
body{font-family:"Mulish",sans-serif;color:var(--text);position:relative}
.page{position:relative;width:1200px;height:3720px;overflow:hidden}
.abs{position:absolute}
h1,h2,h3,.display{font-family:"Montserrat",sans-serif;color:var(--ink);font-weight:400}

/* backgrounds */
.bg-svg{position:absolute;left:0;top:0}

/* header */
.brand{position:absolute;left:180px;top:38px;display:flex;align-items:center;gap:12px;color:var(--white);font-family:"Montserrat",sans-serif;font-weight:500;font-size:33px;letter-spacing:1px}
.brand-dot{width:26px;height:26px;border-radius:50%;background:var(--white)}
.nav{position:absolute;top:52px;left:0;width:1200px;font-family:"Montserrat",sans-serif;font-size:9.5px;font-weight:500;color:var(--white);letter-spacing:.4px}
.nav a{position:absolute;color:var(--white);text-decoration:none;text-transform:uppercase}
.nav .nav-cta{border:1.5px solid var(--white);border-radius:16px;width:76px;height:22px;line-height:19px;text-align:center;top:-4px}

/* hero */
.hero-art{position:absolute;left:130px;top:80px;width:330px;height:440px;border-radius:50%;background:radial-gradient(circle at 50% 45%,rgba(255,255,255,.18),rgba(255,255,255,0) 65%)}
.hero-kicker{position:absolute;left:541px;top:150px;color:var(--white);font-family:"Montserrat",sans-serif;font-size:19px;font-weight:400}
.hero-title{position:absolute;left:537px;top:176px;color:var(--white);font-size:44px;font-weight:500}
.hero-copy{position:absolute;left:543px;top:240px;width:490px;color:var(--white);font-size:14.5px;line-height:29px;font-weight:600}
.btn-white{position:absolute;left:547px;top:355px;width:143px;height:32px;border-radius:18px;background:var(--white);color:var(--pink);font-family:"Montserrat",sans-serif;font-size:9.5px;font-weight:600;letter-spacing:.6px;text-align:center;line-height:32px}
.powered{position:absolute;left:975px;top:463px;font-family:"Montserrat",sans-serif;font-size:12px;color:var(--muted)}
.partner{position:absolute;top:488px;height:36px;border-radius:6px;background:#ececef}

/* features */
.feature{position:absolute;top:665px;width:230px;text-align:center}
.feature-icon{display:block;margin:0 auto;height:70px}
.feature h3{font-family:"Montserrat",sans-serif;font-weight:600;font-size:12px;margin-top:22px}
.feature p{font-size:10px;line-height:20px;margin-top:8px;color:var(--text)}

/* intro sections */
.kicker{font-family:"Montserrat",sans-serif;font-size:10px;letter-spacing:3.5px;color:var(--pink);text-transform:uppercase}
.section-title{font-size:21.5px;line-height:27px;font-weight:400}
.body-copy{font-size:11.5px;line-height:22.5px;color:var(--text)}
.devices{position:absolute;left:95px;top:1040px;width:455px;height:200px}
.btn-pink{position:absolute;left:172px;top:1731px;width:143px;height:34px;border-radius:18px;background:var(--pink);color:var(--white);font-family:"Montserrat",sans-serif;font-size:9.5px;font-weight:600;letter-spacing:.6px;text-align:center;line-height:34px}
.photo{position:absolute;left:592px;top:1386px;width:608px;height:416px;background:linear-gradient(90deg,rgba(255,255,255,1) 0%,rgba(230,214,206,.6) 14%,#c9a794 40%,#8d6a62 62%,#d6a9b7 85%,#e3b5c3 100%)}

/* testimonials */
.center-head{position:absolute;left:0;width:1200px;text-align:center}
.center-head .display{font-size:20px;margin-top:10px;color:#333}
.quote-card{position:absolute;top:2147px;width:232px;background:var(--white);box-shadow:0 2px 10px rgba(0,0,0,.12);text-align:center;padding:40px 20px 0}
.avatar{position:absolute;left:50%;top:-29px;width:58px;height:58px;margin-left:-29px;border-radius:50%;background:#a9a9ab}
.quote-card p{font-size:9.5px;line-height:19px;font-style:italic;color:var(--text)}
.quote-card .who{border-top:1px solid #e6e6e8;margin-top:10px;padding:10px 0 12px;font-size:9.5px;color:#555}
.dots{position:absolute;top:2336px;left:591px;display:flex;gap:5px}
.dots span{width:4px;height:4px;border-radius:50%;background:#c9c9cc}
.dots span.on{background:var(--pink)}

/* news */
.news-band{position:absolute;left:0;top:2404px;width:1200px;height:610px;background:var(--grey-band)}
.news-card{position:absolute;top:2521px;width:267px;height:324px;background:var(--white);box-shadow:0 1px 6px rgba(0,0,0,.08)}
.news-thumb{height:173px;border-bottom:3px solid var(--pink)}
.news-card .date{position:absolute;left:26px;top:216px;font-size:9.5px;color:var(--muted)}
.news-card h3{position:absolute;left:26px;top:238px;font-size:13px;font-weight:500}
.news-card .more{position:absolute;left:26px;top:292px;font-size:7.5px;color:var(--pink);font-weight:600;letter-spacing:.3px}
.btn-outline{position:absolute;left:539px;top:2902px;width:119px;height:31px;background:var(--white);box-shadow:0 1px 6px rgba(0,0,0,.1);font-family:"Montserrat",sans-serif;font-size:9.5px;font-weight:500;color:#333;text-align:center;line-height:31px}

/* contact */
.cta-band{position:absolute;left:0;top:3096px;width:1200px;height:248px;background:linear-gradient(90deg,#dcbccb 0%,#c98aa6 45%,#b84a74 100%)}
.cta-kicker{position:absolute;left:237px;top:3195px;color:var(--white);font-family:"Montserrat",sans-serif;font-size:11.5px;letter-spacing:1.5px}
.cta-title{position:absolute;left:236px;top:3208px;color:var(--white);font-family:"Montserrat",sans-serif;font-size:32px;font-weight:300}
.form-card{position:absolute;left:680px;top:3047px;width:289px;height:354px;background:var(--white);box-shadow:0 2px 12px rgba(0,0,0,.15);overflow:hidden}
.form-card .ring{position:absolute;left:50px;top:-60px;width:330px;height:330px;border-radius:50%;border:55px solid var(--blush)}
.form-card h3{position:absolute;left:35px;top:30px;font-size:15px;color:#333}
.field{position:absolute;left:36px;width:214px;border-bottom:1px solid #e4e4e6;font-size:8.5px;color:#666;padding-bottom:8px}
.check{position:absolute;left:30px;top:3294px;font-size:8px;color:var(--muted);display:flex;align-items:center;gap:8px}
.check i{width:11px;height:11px;border:1px solid #ddd;border-radius:50%;display:block}
.btn-send{position:absolute;left:709px;top:3323px;width:97px;height:29px;border-radius:16px;background:var(--pink);color:var(--white);font-size:10px;text-align:center;line-height:29px}
.hotline{position:absolute;left:830px;top:3326px;font-size:8px;color:#555}
.hotline b{display:block;color:var(--pink);font-size:10px;margin-top:2px}

/* footer */
.foot-col{position:absolute;top:3450px;font-size:9px;color:var(--text)}
.foot-col h4{font-family:"Montserrat",sans-serif;font-size:9.5px;font-weight:700;color:var(--ink);letter-spacing:1.5px;margin-bottom:16px}
.foot-col li{list-style:none;line-height:26px}
.foot-col p{line-height:15px;width:200px}
.foot-col .strong{color:var(--ink);font-weight:700;margin-top:12px}
.contact-row{display:flex;align-items:center;gap:6px}
.bottom-bar{position:absolute;left:237px;top:3630px;display:flex;align-items:center;gap:12px;font-size:8.5px;color:#666}
.bottom-bar .mark{width:22px;height:22px;border-radius:50%;background:var(--pink)}
.bottom-bar b{color:var(--ink)}
</style>
</head>
<body>
<div class="page">

  <!-- decorative backgrounds -->
  <svg class="bg-svg" width="1200" height="3720" viewBox="0 0 1200 3720" aria-hidden="true">
    <defs>
      <linearGradient id="heroGrad" x1="0" y1="0" x2="1" y2="0.4">
        <stop offset="0" stop-color="#d27397"/>
        <stop offset="0.55" stop-color="#c6527f"/>
        <stop offset="1" stop-color="#b83f6c"/>
      </linearGradient>
    </defs>
    <polygon points="0,0 1200,0 1200,420 0,570" fill="url(#heroGrad)"/>
    <path d="M1200 300 A260 260 0 0 0 960 430" fill="none" stroke="rgba(255,255,255,.07)" stroke-width="60"/>
    <circle cx="110" cy="1120" r="330" fill="none" stroke="#fcf0f5" stroke-width="95"/>
    <path d="M0 1490 C300 1440 500 1420 700 1420 L1200 1420 L1200 1880 C1000 1935 400 1950 0 1870 Z" fill="#fcf0f5"/>
  </svg>

  <!-- header -->
  <div class="brand"><span class="brand-dot"></span>KELBRO</div>
  <nav class="nav">
    <a style="left:618px">Startseite</a>
    <a style="left:712px">Funktionen</a>
    <a style="left:813px">Vorteile</a>
    <a style="left:900px">Über uns</a>
    <a style="left:986px">Blog</a>
    <a class="nav-cta" style="left:1037px">Kontakt</a>
  </nav>

  <!-- hero -->
  <div class="hero-art" role="img" aria-label="Illustration mit Geschäftssymbolen: Währung, Kalender, Netzwerk"></div>
  <div class="hero-kicker">Vellorix KLT wird</div>
  <h1 class="hero-title">Quorent Flowdesk</h1>
  <p class="hero-copy">Duis autem vel eum iriure dolor in hendrerit in vulputate velit esse mugiat nuesent luptatum zzril delenit augue duis dolore te feugait nulla facilisi.</p>
  <a class="btn-white">JETZT INFORMIEREN</a>
  <div class="powered">Powered by</div>
  <div class="partner" style="left:736px;width:174px"></div>
  <div class="partner" style="left:924px;width:123px"></div>

  <!-- features -->
  <div class="feature" style="left:236px">
    <svg class="feature-icon" width="100" height="70" viewBox="0 0 100 70">
      <circle cx="50" cy="38" r="24" fill="#c04a78"/>
      <circle cx="50" cy="38" r="9" fill="none" stroke="#fff" stroke-width="5"/>
      <g stroke="#fff" stroke-width="4"><line x1="50" y1="22" x2="50" y2="27"/><line x1="50" y1="49" x2="50" y2="54"/><line x1="34" y1="38" x2="39" y2="38"/><line x1="61" y1="38" x2="66" y2="38"/></g>
      <line x1="10" y1="44" x2="24" y2="44" stroke="#f0c6d6" stroke-width="3"/><line x1="76" y1="44" x2="92" y2="44" stroke="#f0c6d6" stroke-width="3"/>
      <circle cx="40" cy="6" r="2.5" fill="#e9a9c0"/>
    </svg>
    <h3>Bessere Kontrolle</h3>
    <p>Consetetur sadipscing elitr, sed diam nonumy eirmod tempor invidunt ut labore et dolore erat, sed diam voluptua.</p>
  </div>
  <div class="feature" style="left:486px">
    <svg class="feature-icon" width="100" height="70" viewBox="0 0 100 70">
      <g fill="#c04a78"><ellipse cx="40" cy="58" rx="10" ry="4"/><ellipse cx="40" cy="50" rx="10" ry="4"/><ellipse cx="62" cy="58" rx="10" ry="4"/><ellipse cx="62" cy="50" rx="10" ry="4"/><ellipse cx="62" cy="42" rx="10" ry="4"/><ellipse cx="62" cy="34" rx="10" ry="4"/></g>
      <polyline points="14,36 30,26 42,30 70,8" fill="none" stroke="#c04a78" stroke-width="2.5"/>
      <polygon points="70,4 76,6 72,12" fill="#c04a78"/>
      <line x1="8" y1="56" x2="24" y2="56" stroke="#f0c6d6" stroke-width="3"/>
    </svg>
    <h3>Höhere Margen</h3>
    <p>Consetetur sadipscing elitr, sed diam nonumy eirmod tempor invidunt ut labore et dolore erat, sed diam voluptua.</p>
  </div>
  <div class="feature" style="left:734px">
    <svg class="feature-icon" width="100" height="70" viewBox="0 0 100 70">
      <rect x="26" y="12" width="48" height="34" fill="none" stroke="#c04a78" stroke-width="3"/>
      <g fill="#c04a78"><rect x="38" y="32" width="4" height="10"/><rect x="45" y="27" width="4" height="15"/><rect x="52" y="22" width="4" height="20"/><rect x="59" y="18" width="4" height="24"/></g>
      <line x1="50" y1="46" x2="42" y2="62" stroke="#c04a78" stroke-width="3"/><line x1="50" y1="46" x2="58" y2="62" stroke="#c04a78" stroke-width="3"/>
      <line x1="22" y1="12" x2="78" y2="12" stroke="#c04a78" stroke-width="3"/>
      <circle cx="16" cy="22" r="2.5" fill="#e9a9c0"/><circle cx="86" cy="20" r="2.5" fill="#e9a9c0"/>
    </svg>
    <h3>Mehr Wachstum</h3>
    <p>Consetetur sadipscing elitr, sed diam nonumy eirmod tempor invidunt ut labore et dolore erat, sed diam voluptua.</p>
  </div>

  <!-- product section -->
  <div class="devices" role="img" aria-label="Laptop und Tablet mit Dashboard der Software">
    <svg width="455" height="200" viewBox="0 0 455 200">
      <rect x="0" y="0" width="404" height="200" rx="10" fill="#232529"/>
      <rect x="14" y="24" width="378" height="176" fill="#f4f6f8"/>
      <rect x="205" y="80" width="250" height="120" rx="9" fill="#232529"/>
      <rect x="215" y="92" width="232" height="108" fill="#eef2f5"/>
    </svg>
  </div>
  <div class="abs kicker" style="left:610px;top:990px">Lorem ipsum dolor sit amet</div>
  <h2 class="abs section-title" style="left:610px;top:1008px;width:440px">Lorem ipsum dolor sit amet consetetur sadipscing elitr</h2>
  <p class="abs body-copy" style="left:610px;top:1073px;width:425px">Ut wisi enim ad minim veniam, quis nostrud exerci tation ullamcorper suscipit lobortis nisl ut aliquip ex ea commodo consequat. Dat nulla facili- sis at vero eros et accumsan et iusto odio dignissim qui blandit praesent luptatum zzril delenit augue duis dolore te feugait nulla facilisi.</p>
  <p class="abs body-copy" style="left:610px;top:1183px;width:425px">Ut wisi enim ad minim veniam, quis nostrud exerci tation ullamcorper suscipit lobortis nisl ut aliquip ex ea commodo consequat.</p>

  <!-- people section -->
  <div class="photo" role="img" aria-label="Foto: zwei Kollegen arbeiten gemeinsam am Laptop"></div>
  <h2 class="abs section-title" style="left:169px;top:1494px;width:430px">Lorem ipsum dolor sit amet consetetur sadipscing elitr</h2>
  <p class="abs body-copy" style="left:170px;top:1561px;width:425px">Ut wisi enim ad minim veniam, quis nostrud exerci tation ullamcorper suscipit lobortis nisl ut aliquip ex ea commodo consequat. Dat nulla facili- sis at vero eros et accumsan et iusto odio dignissim qui blandit praesent luptatum zzril delenit augue duis dolore te feugait nulla facilisi.</p>
  <p class="abs body-copy" style="left:170px;top:1670px;width:425px">Ut wisi enim ad minim veniam, quis nostrud exerci tation ullamcorper suscipit lobortis nisl ut aliquip ex ea commodo consequat.</p>
  <a class="btn-pink">JETZT INFORMIEREN ▸</a>

  <!-- testimonials -->
  <div class="center-head" style="top:2026px">
    <div class="kicker">Feedbacks</div>
    <div class="display">das sagen unsere Kunden</div>
  </div>
  <div class="quote-card" style="left:237px">
    <span class="avatar"></span>
    <p>“ Ut wisi enim ad minim veniam, quis nostrud exerci tation ullamcorper suscipit lobortis uip exconsequat. ”</p>
    <div class="who">Mira Hollberg</div>
  </div>
  <div class="quote-card" style="left:487px">
    <span class="avatar"></span>
    <p>“ Nam liber tempor cum soluta nobis eleifend option congue nihil imperdiet doming id quo nostrp ex ea con- sequat. ”</p>
    <div class="who">Tom Gerlach</div>
  </div>
  <div class="quote-card" style="left:736px">
    <span class="avatar"></span>
    <p>“ Nam liber tempor cum soluta nobis eleifend option congued quo nostrp ex ea commodo consequat. ”</p>
    <div class="who">Jana Kellner</div>
  </div>
  <div class="dots"><span></span><span></span><span class="on"></span></div>

  <!-- news -->
  <div class="news-band"></div>
  <div class="center-head" style="top:2433px">
    <div class="kicker">Aktuelles</div>
    <div class="display">rund um das ERP</div>
  </div>
  <article class="news-card" style="left:169px">
    <div class="news-thumb" role="img" aria-label="Vorschau der neuen Startseite in Pink" style="background:linear-gradient(170deg,#d06e94 0%,#c04a78 62%,#fff 62%)"></div>
    <div class="date">08.05.2018</div>
    <h3>Unser neue Homepage ist Online</h3>
    <div class="more">WEITERLESEN</div>
  </article>
  <article class="news-card" style="left:464px">
    <div class="news-thumb" role="img" aria-label="Foto: Bücherregale in einer Bibliothek" style="background:linear-gradient(180deg,#5b5d62 0%,#8f7a66 45%,#b39b82 100%)"></div>
    <div class="date">08.05.2018</div>
    <h3>Lorom ipsum dolor</h3>
    <div class="more">WEITERLESEN</div>
  </article>
  <article class="news-card" style="left:758px">
    <div class="news-thumb" style="background:#000;position:relative">
      <span style="position:absolute;left:0;width:267px;top:76px;text-align:center;color:#fff;font-family:'Montserrat',sans-serif;font-size:18px">Vellorix Nexa</span>
    </div>
    <div class="date">08.05.2018</div>
    <h3>Lorom ipsum dolor to</h3>
    <div class="more">WEITERLESEN</div>
  </article>
  <a class="btn-outline">mehr von Blog</a>

  <!-- contact -->
  <div class="cta-band"></div>
  <div class="cta-kicker">350.000 VELLORIX KLT-KUNDEN</div>
  <div class="cta-title">und wann sind Sie dran?</div>
  <form class="form-card">
    <span class="ring"></span>
    <h3>Jetzt unverbindlich informieren</h3>
    <div class="field" style="top:70px">Firmenname*</div>
    <div class="field" style="top:104px">Ihr Vorname</div>
    <div class="field" style="top:136px">Ihr Nachname*</div>
    <div class="field" style="top:170px">E-Mail Adresse*</div>
    <div class="field" style="top:213px">Telefonnummer</div>
    <div class="check" style="top:247px"><i></i>Ich bitte um eine Rückruf</div>
  </form>
  <a class="btn-send">Kontaktieren</a>
  <div class="hotline">noch Fragen?<b>(0)900 / 12 34 56 78</b></div>

  <!-- footer -->
  <div class="foot-col" style="left:237px">
    <h4>WARUM Kelbro GmbH?</h4>
    <p>Mit 11 Jahren Gesamterfahrung im Vello- rix KLT Umfeld, ist kein Projekt zu klein oder zu kompliziert für uns.</p>
    <p class="strong">Sprechen Sie uns an!</p>
  </div>
  <div class="foot-col" style="left:475px">
    <h4>UNTERNEHMEN</h4>
    <ul><li>Über uns</li><li>Leistungen</li><li>Preise</li><li>Vorteile</li></ul>
  </div>
  <div class="foot-col" style="left:635px">
    <h4>GESETZLICHES</h4>
    <ul><li>Impressum</li><li>Datenschutz</li><li>AGBs</li><li>Kontakt</li></ul>
  </div>
  <div class="foot-col" style="left:801px">
    <h4>KONTAKT</h4>
    <ul>
      <li class="contact-row"><svg width="9" height="11" viewBox="0 0 9 11"><path d="M4.5 0A4 4 0 0 0 .5 4c0 3 4 7 4 7s4-4 4-7a4 4 0 0 0-4-4z" fill="#c04a78"/><circle cx="4.5" cy="4" r="1.5" fill="#fff"/></svg>Falkenstr. 9, DE-90411 Lindenau</li>
      <li class="contact-row"><svg width="9" height="9" viewBox="0 0 9 9"><path d="M1 1l2-.5 1 2-1 1a5 5 0 0 0 2.5 2.5l1-1 2 1L8 8C4 8 1 5 1 1z" fill="#c04a78"/></svg>+49 100 200 300</li>
      <li class="contact-row"><svg width="9" height="9" viewBox="0 0 9 9"><circle cx="4.5" cy="4.5" r="3.5" fill="none" stroke="#c04a78" stroke-width="1.2"/><circle cx="4.5" cy="4.5" r="1.3" fill="#c04a78"/></svg>hallo@kelbrotech.eu</li>
    </ul>
  </div>
  <div class="bottom-bar"><span class="mark"></span><span>Copyright 2018 © <b>Kelbro GmbH</b> | Alle Rechte vorbehalten</span></div>

</div>
</body>
</html>
```